Design a cover that embodies the concept of healing by Walking Out of Shadows

Subtitle: How to use tapping, applied kinesiology, and Chinese medicine to heal your body, free your mind and live in peace.

Tapping (Emotional Freedom Technique) is a modern mix of psychology and Chinese medicine that helps people to release the emotions they have inside that are contributing to the depression and anxiety they feel. Applied kinesiology or muscle testing is a biofeedback tool which helps to extract information from the body that can help people to profoundly heal. It can be used to determine whether heavy metals, heavy chemicals, food sensitivities or pathogens are causing the body problems. It can also be used to determine which supplements can help someone heal. This tool also can be used to identify emotions and memories that are also causing someone problems. Lastly, Chinese medicine uses food therapy, herbal formulas, meditation, tai chi (meditative movement), cupping and other tools to help people to be free of depression. This book is written to be information but also details my own personal journey of how I was able to heal from 11 years of heavy depression through the use of these tools.

The heart of the book is about emotional release, emotional freedom and emotional healing. You can surrender, release or let go of emotions and feel better very quickly. This certainly was my experience.

I would like the front and back cover to each be 8.5" x 5.5". I still have to get an ISBN number for the back page as well. Here is the text that I would like on the back cover for now: Millions of people feel the pain, loneliness, and agony of anxiety and depression every day. Many turn to Western medicine in the hopes that a pill will ease the pain and make the problem go away. Oftentimes, this only makes matters worse and doesn’t address the root cause. No one should have to struggle like this when natural answers exist that can address the physical, energetic, emotional, or spiritual causes of anxiety and depression. For 11 long years, Dr. Mervin personally struggled with heavy depression until he discovered answers that helped him to completely heal. Walking Out of Shadows is a guide that will help you discover - The two root physical causes of depression and exactly what to do to start healing today - How the negative emotions we have stored within from trauma and bad experiences can drive depression - Tools from Chinese medicine, applied kinesiology, and tapping to help you free your mind and live in peace - An actionable plan to help you let go of the pain, suffering, and negative emotions from your past Whether you feel depressed and anxious or know someone who struggles with these issues, Walking Out of Shadows will transform how you think about depression and will give you the tools to heal so that you can be free and live in peace. Dr. Mervin Holloway is a board-certified acupuncture physician licensed in the state of Florida. He received his training at the Marlow Institute of Restorative Health. He also graduated with a master’s degree in counseling and psychology from Cedarbrook School of Ministry. His mission is to help people transform their health and improve the quality of their life naturally. He lives in Orlando, FL where he runs a holistic medical clinic called Brightpath Wellness Center. www.drmervinholloway.example Instagram: drmervinholloway Facebook: brightpathwellnesscenter

Target Market(s)

Those who suffer from depression and anxiety and want to heal naturally

Industry/Entity Type

Health And Wellness

Requirements
Must have
• My picture should be small and go on the back cover next to the information about me. The front cover would be all graphical. Thank you. On the front cover my name should be posted as "Dr. Mervin Holloway, AP, MA"

```html
<!DOCTYPE html>
<html lang="en">
<head>
<meta charset="utf-8">
<title>Walking Out of Shadows – Cover Spread</title>
<link rel="stylesheet" href="https://fonts.googleapis.com/css2?family=Oswald:wght@400;500;700&display=swap">
<style>
  :root {
    --page-bg: #eeeeee;
    --sky-deep: #1c6dad;
    --sky-mid: #4a9ad2;
    --sky-light: #a9d3ee;
    --earth-light: #8a4a2a;
    --earth-dark: #3d1c10;
    --ink: #ffffff;
    --shadow: #0b2f66;
    --isbn-box: #ffffff;
    --portrait-a: #d9b48a;
    --portrait-b: #6f8f4a;
  }
  * { margin: 0; padding: 0; box-sizing: border-box; }
  html, body { width: 693px; height: 1200px; overflow: hidden; background: var(--page-bg); }
  body { position: relative; font-family: "Oswald", sans-serif; color: var(--ink); }

  .spread { position: absolute; left: 0; top: 348px; width: 693px; height: 504px; overflow: hidden; }
  .spread-art {
    position: absolute; inset: 0;
    background: linear-gradient(180deg, var(--sky-deep) 0%, var(--sky-mid) 30%, var(--sky-light) 60%, var(--sky-mid) 76%, var(--earth-light) 84%, var(--earth-dark) 100%);
  }

  .smallcaps { font-variant: small-caps; text-shadow: 1px 1px 2px var(--shadow); }

  /* Back cover */
  .back { position: absolute; left: 0; top: 0; width: 328px; height: 504px; }
  .back-title { position: absolute; left: 70px; top: 22px; width: 180px; text-align: right; font-weight: 700; line-height: 0.9; }
  .back-title .line-1 { display: block; font-size: 27px; }
  .back-title .line-2 { display: block; font-size: 40px; }
  .back-block { position: absolute; left: 19px; width: 296px; font-size: 8.6px; line-height: 11.7px; font-weight: 500; }
  .back-intro { top: 100px; text-align: justify; }
  .back-list-intro { top: 181px; text-align: center; }
  .back-list { top: 193px; list-style: none; text-align: center; }
  .back-closing { top: 274px; text-align: justify; }
  .bio { position: absolute; left: 19px; top: 316px; width: 170px; font-size: 8.6px; line-height: 11.6px; font-weight: 500; text-align: justify; }
  .contacts { position: absolute; left: 14px; top: 436px; width: 180px; font-size: 7.2px; line-height: 11.5px; font-weight: 700; text-align: center; }
  .author-portrait { position: absolute; left: 195px; top: 312px; width: 117px; height: 105px; background: linear-gradient(160deg, var(--portrait-b), var(--portrait-a)); }
  .isbn-box { position: absolute; left: 195px; top: 422px; width: 117px; height: 68px; background: var(--isbn-box); }

  /* Spine */
  .spine { position: absolute; left: 328px; top: 0; width: 36px; height: 504px; }
  .spine-text { position: absolute; left: 7px; writing-mode: vertical-rl; font-weight: 700; font-size: 17px; line-height: 1; white-space: nowrap; }
  .spine-author { top: 36px; }
  .spine-title { top: 210px; }

  /* Front cover */
  .front { position: absolute; left: 364px; top: 0; width: 329px; height: 504px; }
  .front-author { position: absolute; left: 0; top: 44px; width: 329px; text-align: center; font-weight: 700; font-size: 22px; }
  .front-title { position: absolute; left: 28px; top: 132px; width: 282px; text-align: right; font-weight: 700; line-height: 0.88; }
  .front-title .line-1 { display: block; font-size: 50px; }
  .front-title .line-2 { display: block; font-size: 80px; }
  .front-subtitle { position: absolute; left: 24px; top: 430px; width: 298px; font-size: 16px; line-height: 27px; font-weight: 500; text-align: justify; text-align-last: justify; }
</style>
</head>
<body>
  <main class="spread">
    <div class="spread-art" role="img" aria-label="Photograph of a blue cloudy sky over a red earth hill with a person meditating on its top"></div>

    <section class="back">
      <h2 class="back-title smallcaps"><span class="line-1">Walking Out of</span><span class="line-2">Shadows</span></h2>
      <p class="back-block back-intro smallcaps">Millions of people feel the pain, loneliness, and agony of anxiety and depression every day. Many turn to Western medicine in the hopes that a pill will ease the pain and make the problem go away. Oftentimes, this only makes matters worse and doesn’t address the root cause. No one should have to struggle like this when natural answers exist that can address the physical, energetic, emotional, or spiritual causes of anxiety and depression. For 11 long years, Dr. Mervin personally struggled with heavy depression until he discovered answers that helped him to completely heal.</p>
      <p class="back-block back-list-intro smallcaps">Walking Out of Shadows is a guide that will help you discover:</p>
      <ul class="back-block back-list smallcaps">
        <li>- The two root physical causes of depression and exactly what to do to start healing today</li>
        <li>- How the negative emotions we have stored within from trauma and bad experiences can drive depression</li>
        <li>- Tools from Chinese medicine, applied kinesiology, and tapping to help you free your mind and live in peace</li>
        <li>- An actionable plan to help you let go of the pain, suffering, and negative emotions from your past</li>
      </ul>
      <p class="back-block back-closing smallcaps">Whether you feel depressed and anxious or know someone who struggles with these issues, Walking Out of Shadows will transform how you think about depression and will give you the tools to heal so that you can be free and live in peace.</p>
      <p class="bio smallcaps">Dr. Mervin Holloway is a board-certified acupuncture physician licensed in the state of Florida. He received his training at the Marlow Institute of Restorative Health. He also graduated with a master’s degree in counseling and psychology from Cedarbrook School of Ministry. His mission is to help people transform their health and improve the quality of their life naturally. He lives in Orlando, FL where he runs a holistic medical clinic called Brightpath Wellness Center.</p>
      <div class="author-portrait" role="img" aria-label="Portrait photograph of the author"></div>
      <div class="isbn-box"></div>
      <p class="contacts smallcaps">www.drmervinholloway.example<br>Instagram: drmervinholloway<br>Facebook: brightpathwellnesscenter</p>
    </section>

    <section class="spine">
      <span class="spine-text spine-author smallcaps">Dr. Mervin Holloway</span>
      <span class="spine-text spine-title smallcaps">Walking Out of Shadows</span>
    </section>

    <section class="front">
      <p class="front-author smallcaps">Dr. Mervin Holloway, AP, MA</p>
      <h1 class="front-title smallcaps"><span class="line-1">Walking Out of</span><span class="line-2">Shadows</span></h1>
      <p class="front-subtitle smallcaps">How to use tapping, applied kinesiology, and Chinese medicine to heal your body, free your mind and live in peace.</p>
    </section>
  </main>
</body>
</html>
```